New, modern business card for growing audiology practice

We need a new business card for our audiology practice. Our logo and website have recently changed (more modern) and we want our business cards to reflect this change.
We conduct hearing tests, perform earwax removals, and fit & dispense hearing aids to our patients. We are a family owned practice in which the owner is the one who works directly with the patient. I have attached logos in various formats to use, as well as two ideas I found on this website; as well as a scanned copy of our current logo. Good luck!

Industry/Entity Type

Business

Contact Information for Business Card

Company name: Tolvera Hearing Center
Provider name: Peter Wolstenby, Au.D. F/NSB
Phone number: (440) 683-5127
Address: 837 W. Lindell Ave. Marlow Heights, OH 44187
email: tolverahearing@postvane.com
website: tolverahearing.com

Colors
000000
aaaaaa
dbdbdb
cacaca
9bcb3c
afd23c
cadf82
b1b1b1

Requirements
Must have
• My card must include information in the "details" section. In the attached images, I found a few that I liked and I would like to model after - "brisky bouncin'" and "Sound Method Center".
• Must be horizontal.
• Must include logos provided. I uploaded them in various file formats and various ways.
• Must match logo font, if possible, if not, please get as close as you can.
Nice to have
• I really like the idea of having a color on one side with just the logo and company name and the contact information and provider name on the other side. I also really like the idea of having the main color dominating on the logo/company side with accent of that same color on the contact side of the card.
Should not have
• Must not be vertical.

```html
<!DOCTYPE html>
<html lang="en">
<head>
<meta charset="utf-8">
<title>Tolvera Hearing Center – Business Card</title>
<link rel="stylesheet" href="https://fonts.googleapis.com/css2?family=Cabin:wght@500&family=Roboto+Condensed:wght@700&family=Roboto:wght@400;500&display=swap">
<style>
  :root {
    --stage: #2a2a2a;
    --card-dark: #161616;
    --card-light: #f7f7f5;
    --green: #7fae2e;
    --green-light: #9bcb3c;
    --white: #ffffff;
    --text-dark: #1a1a1a;
    --text-grey: #8a8a8a;
    --rule: #b1b1b1;
  }
  * { box-sizing: border-box; margin: 0; padding: 0; }
  html, body {
    width: 1200px; height: 900px; overflow: hidden;
    background: var(--stage);
  }
  .stage {
    width: 1200px; height: 900px;
    display: flex; flex-direction: column; align-items: center; justify-content: center;
    gap: 40px;
  }
  .card {
    width: 700px; height: 400px;
    position: relative;
    box-shadow: 0 10px 30px rgba(0,0,0,.45);
  }
  .card-front {
    background: var(--card-dark);
    display: flex; flex-direction: column; align-items: center; justify-content: center;
  }
  .brand {
    display: flex; align-items: center; gap: 16px;
    margin-top: -10px;
  }
  .brand-dot {
    width: 30px; height: 30px; border-radius: 50%;
    background: var(--green-light);
  }
  .brand-name {
    font-family: "Cabin", sans-serif; font-weight: 500;
    font-size: 34px; letter-spacing: 0.5px;
    color: var(--white); text-transform: uppercase;
  }
  .front-web {
    margin-top: 56px;
    font-family: "Roboto", sans-serif; font-weight: 500;
    font-size: 16px; letter-spacing: 4px;
    color: var(--white);
  }
  .front-web .accent { color: var(--green-light); }

  .card-back {
    background: var(--card-light);
    display: flex; align-items: center;
  }
  .provider {
    width: 340px; padding-right: 28px;
    text-align: right;
  }
  .provider-name {
    font-family: "Roboto Condensed", sans-serif; font-weight: 700;
    font-size: 36px; line-height: 1; color: var(--green);
    text-transform: uppercase;
  }
  .provider-title {
    margin-top: 6px;
    font-family: "Roboto", sans-serif; font-weight: 500;
    font-size: 16px; color: var(--text-dark); letter-spacing: 0.5px;
  }
  .divider {
    width: 2px; height: 140px; background: var(--rule);
  }
  .contact {
    padding-left: 26px;
    font-family: "Roboto", sans-serif; font-weight: 400;
    font-size: 16px; line-height: 1.3; color: var(--text-grey);
  }
  .contact-address { margin-bottom: 14px; }
  .contact-row { display: flex; align-items: center; gap: 10px; }
  .contact-row svg { width: 14px; height: 14px; flex: none; fill: var(--green); }
  .contact-row .icon-mail-flap { fill: none; stroke: var(--card-light); stroke-width: 2; }
</style>
</head>
<body>
<main class="stage">
  <section class="card card-front">
    <div class="brand">
      <span class="brand-dot"></span>
      <span class="brand-name">Tolvera Hearing Center</span>
    </div>
    <p class="front-web">www.<span class="accent">tolverahearing</span>.com</p>
  </section>

  <section class="card card-back">
    <div class="provider">
      <h1 class="provider-name">Peter Wolstenby</h1>
      <p class="provider-title">AU.D. F/NSB</p>
    </div>
    <div class="divider"></div>
    <div class="contact">
      <p class="contact-address">837 W. Lindell Ave.<br>Marlow Heights, OH 44187</p>
      <p class="contact-row">
        <svg viewBox="0 0 24 24" aria-hidden="true"><path d="M6.6 10.8a15.1 15.1 0 0 0 6.6 6.6l2.2-2.2a1 1 0 0 1 1-.25 11.4 11.4 0 0 0 3.6.57 1 1 0 0 1 1 1V20a1 1 0 0 1-1 1A17 17 0 0 1 3 4a1 1 0 0 1 1-1h3.5a1 1 0 0 1 1 1c0 1.25.2 2.45.57 3.57a1 1 0 0 1-.25 1z"/></svg>
        (440) 683-5127
      </p>
      <p class="contact-row">
        <svg viewBox="0 0 24 24" aria-hidden="true"><rect x="2" y="5" width="20" height="14" rx="1"/><path class="icon-mail-flap" d="M3 6l9 7 9-7"/></svg>
        tolverahearing@postvane.com
      </p>
      <p class="contact-row">
        <svg viewBox="0 0 24 24" aria-hidden="true"><circle cx="12" cy="12" r="10"/></svg>
        tolverahearing.com
      </p>
    </div>
  </section>
</main>
</body>
</html>
```